Semi-anonymous photo sharing and messaging app

Design app interface. App is needed for semi-anonymous communication.

For instance if you are on a tour bus, and you just met some people there. You want to send them pictures, but you don't want to give your chatterbox / email / phone number. So instead you use this app - current name is "eLumix" but you can also suggest a name if it fits really well with the theme of the design.

The initial version of the app is in the vantor store
https://apps.vantorhub.example/store/apps/details?id=com.qz7mwplk3rt9bvne5hsyc

the web version of this app is located here
https://tallbluekites.example/

it is called Tall Blue Kites, because the password is four common words, and if you know those words, you can open the chat room.

As you can see app looks very poorly, and needs to be designed from bottom up. App should look nothing like it looks now. it should have original and easily recognizable feel to it.

I'm attaching screen-shots of the current app. Two screens - you enter password on one screen (or choose one of the existing "rooms") - you chat with peers on the second screen

It should be something neutral, so it's mainly for travellers, but could be used by anyone else. It should have vibe of comfort and security, but at the same time adventure and fun.

Please come back with more questions!

Target Market(s)

Travellers, mostly
single, groups,

Industry/Entity Type

Communication

Font styles to use
Sans Serif

Requirements
Must have
• original, light feel
• recognizable
• unique

```html
<!DOCTYPE html>
<html lang="en">
<head>
<meta charset="utf-8">
<title>Enter Words</title>
<link href="https://fonts.googleapis.com/css2?family=Roboto:wght@400;500;700&display=swap" rel="stylesheet">
<style>
  :root {
    --blue: #1590e4;
    --blue-light: #2aa7f2;
    --blue-dark: #0f80d6;
    --ink: #222222;
    --ink-soft: #444444;
    --placeholder: #9a9a9a;
    --field-border: #b9bec4;
    --bar-grey: rgba(196, 198, 200, 0.72);
    --white: #ffffff;
  }
  * { box-sizing: border-box; margin: 0; padding: 0; }
  html, body { width: 676px; height: 1200px; overflow: hidden; background: var(--white); }
  body { font-family: 'Roboto', Arial, sans-serif; color: var(--ink); }

  .screen {
    position: absolute; left: 0; top: 0;
    width: 640px; height: 1136px;
    transform: scale(1.05625); transform-origin: 0 0;
    overflow: hidden;
  }
  .backdrop {
    position: absolute; inset: 0;
    background: linear-gradient(160deg, rgba(250,236,214,0.9) 0%, rgba(240,240,242,0.85) 35%, rgba(226,228,232,0.85) 60%, rgba(236,226,218,0.9) 100%);
  }

  .top-bar {
    position: absolute; left: 0; top: 0; width: 640px; height: 112px;
    background: var(--bar-grey);
  }
  .status-bar {
    position: absolute; left: 0; top: 0; width: 640px; height: 40px;
    font-size: 21px; font-weight: 400; color: #111;
  }
  .status-bar .carrier { position: absolute; left: 12px; top: 13px; display: flex; align-items: center; gap: 6px; }
  .status-bar .time { position: absolute; left: 0; right: 0; top: 13px; text-align: center; font-weight: 500; }
  .status-bar .power { position: absolute; right: 10px; top: 11px; display: flex; align-items: center; gap: 8px; }

  .inbox-icon { position: absolute; left: 34px; top: 58px; }
  .settings-icon { position: absolute; left: 566px; top: 58px; }

  .avatar {
    position: absolute; left: 232px; top: 122px; width: 176px; height: 176px;
    border-radius: 50%; border: 4px solid var(--white);
    background: radial-gradient(circle at 50% 40%, #8a6a50 0%, #4a6a3a 55%, #2c3e2a 100%);
  }
  .welcome {
    position: absolute; left: 0; right: 0; top: 316px;
    text-align: center; font-size: 25px; font-weight: 500; color: var(--ink);
  }

  .word-field {
    position: absolute; left: 60px; width: 520px; height: 82px;
    background: var(--white); border: 1px solid var(--field-border); border-radius: 4px;
    overflow: hidden;
  }
  .word-field span {
    position: absolute; left: 15px; top: 23px;
    font-size: 31px; color: var(--placeholder);
  }
  .word-field::after {
    content: ""; position: absolute; right: 0; top: 0; width: 96px; height: 100%;
    background: var(--blue);
  }
  .field-1 { top: 358px; } .field-2 { top: 468px; } .field-3 { top: 580px; } .field-4 { top: 690px; }

  .action {
    position: absolute; top: 812px; height: 82px;
    background: linear-gradient(180deg, var(--blue-light), var(--blue-dark));
    border: 1px solid #0d79c8; border-radius: 3px;
    color: var(--white); font-size: 29px; font-weight: 500;
    display: flex; align-items: center; justify-content: center;
  }
  .action-enter { left: 60px; width: 186px; }
  .action-generate { left: 281px; width: 297px; }

  .recent { position: absolute; left: 63px; top: 910px; }
  .recent h2 { font-size: 28px; font-weight: 500; color: var(--ink); margin-bottom: 6px; }
  .recent li { list-style: none; font-size: 24px; color: var(--ink-soft); line-height: 36px; }

  .tab-bar {
    position: absolute; left: 0; top: 1041px; width: 640px; height: 95px;
    background: var(--blue); display: flex;
  }
  .tab {
    flex: 1; position: relative; border-right: 1px solid rgba(0,60,120,0.35);
    color: var(--white); font-size: 13px; font-weight: 500; text-align: center;
  }
  .tab:last-child { border-right: none; }
  .tab svg { position: absolute; left: 50%; top: 10px; transform: translateX(-50%); }
  .tab .label { position: absolute; left: 0; right: 0; top: 71px; }
</style>
</head>
<body>
<div class="screen">
  <div class="backdrop" role="img" aria-label="Faded collage of travel photos of people and places"></div>

  <div class="top-bar">
    <div class="status-bar">
      <div class="carrier">
        <svg width="58" height="14" viewBox="0 0 58 14"><g fill="#111"><circle cx="6" cy="7" r="5"/><circle cx="17" cy="7" r="5"/><circle cx="28" cy="7" r="5"/></g><g fill="none" stroke="#111" stroke-width="1.4"><circle cx="39" cy="7" r="4.4"/><circle cx="50" cy="7" r="4.4"/></g></svg>
        <span>KESTRIL</span>
        <svg width="22" height="16" viewBox="0 0 22 16"><g fill="none" stroke="#111" stroke-width="2.4" stroke-linecap="round"><path d="M2 6a13 13 0 0 1 18 0"/><path d="M5.5 9.5a8 8 0 0 1 11 0"/></g><circle cx="11" cy="13.5" r="2" fill="#111"/></svg>
      </div>
      <div class="time">4:21 PM</div>
      <div class="power">
        <svg width="12" height="20" viewBox="0 0 12 20"><path d="M1 5l10 10-5 4V1l5 4L1 15" fill="none" stroke="#777" stroke-width="1.6"/></svg>
        <span>100%</span>
        <svg width="46" height="20" viewBox="0 0 46 20"><rect x="1" y="1" width="40" height="18" rx="3" fill="none" stroke="#111" stroke-width="1.6"/><rect x="3.5" y="3.5" width="35" height="13" rx="1.5" fill="#111"/><rect x="42" y="6" width="3" height="8" rx="1" fill="#111"/></svg>
      </div>
    </div>

    <svg class="inbox-icon" width="62" height="42" viewBox="0 0 62 42" aria-label="Messages, 2 unread">
      <g fill="none" stroke="#222" stroke-width="2">
        <rect x="1" y="9" width="46" height="31" rx="1"/>
        <path d="M1 10l23 17 23-17"/>
        <circle cx="52" cy="9" r="8" fill="#e8e8e8"/>
      </g>
      <text x="52" y="14" font-size="13" text-anchor="middle" fill="#222" font-family="Roboto, sans-serif">2</text>
    </svg>
    <svg class="settings-icon" width="46" height="46" viewBox="0 0 46 46" aria-label="Settings">
      <g fill="none" stroke="#222" stroke-width="2">
        <path d="M20 3h6l1.5 5.5 4 1.7 5-2.8 4.2 4.2-2.8 5 1.7 4L45 20v6l-5.5 1.5-1.7 4 2.8 5-4.2 4.2-5-2.8-4 1.7L26 45h-6l-1.5-5.5-4-1.7-5 2.8-4.2-4.2 2.8-5-1.7-4L1 26v-6l5.5-1.5 1.7-4-2.8-5 4.2-4.2 5 2.8 4-1.7z"/>
        <circle cx="23" cy="23" r="8"/>
      </g>
    </svg>
  </div>

  <div class="avatar" role="img" aria-label="Profile photo of the user"></div>
  <p class="welcome">Welcome Marisol Keane!</p>

  <div class="word-field field-1"><span>Word 1</span></div>
  <div class="word-field field-2"><span>Word 2</span></div>
  <div class="word-field field-3"><span>Word 3</span></div>
  <div class="word-field field-4"><span>Word 4</span></div>

  <div class="action action-enter">ENTER</div>
  <div class="action action-generate">GENERATE WORDS</div>

  <section class="recent">
    <h2>Recent</h2>
    <ul>
      <li>1. back, class, horse, husband.</li>
      <li>2. amount, firm, industry, pupil.</li>
    </ul>
  </section>

  <nav class="tab-bar">
    <div class="tab">
      <svg width="56" height="56" viewBox="0 0 56 56" aria-label="Words"><g fill="none" stroke="#fff" stroke-width="2"><circle cx="28" cy="28" r="26"/><rect x="18" y="26" width="20" height="16" rx="2"/><path d="M22 26v-5a6 6 0 0 1 12 0v5"/></g></svg>
      <span class="label">4 WORDS</span>
    </div>
    <div class="tab">
      <svg width="56" height="56" viewBox="0 0 56 56"><g fill="none" stroke="#fff" stroke-width="2"><path d="M5 6h46v32H22l-10 11v-11H5z"/><path d="M13 17h30M13 24h30M13 31h30"/></g></svg>
      <span class="label">CHAT ROOM</span>
    </div>
    <div class="tab">
      <svg width="56" height="56" viewBox="0 0 56 56"><g fill="none" stroke="#fff" stroke-width="2"><circle cx="28" cy="17" r="11"/><path d="M6 52c0-14 10-22 22-22s22 8 22 22z"/></g></svg>
      <span class="label">PROFILE</span>
    </div>
    <div class="tab">
      <svg width="56" height="56" viewBox="0 0 56 56"><circle cx="28" cy="28" r="26" fill="none" stroke="#fff" stroke-width="2"/><circle cx="28" cy="17" r="2" fill="#fff"/><path d="M28 24v18" stroke="#fff" stroke-width="2"/></svg>
      <span class="label">ABOUT</span>
    </div>
  </nav>
</div>
</body>
</html>
```